Vellisant - Quality health delivered at your door

Vellisant offers home and Community Based Services for adults who wish to continue live independently in their communities. We increase accessibility to health care, reduce health care delivery gap, reduce mortality and morbidity, reduce health while promoting healthy living in the comfort of our patients communities or homes.

We provide on site services and deliver high quality healthcare at your door. Our experienced physicians coordinate care with our certified nurse practitioners and provide chronic care management, physical therapy, rehabilitation and medications management.

Target Market(s)

Older population living in independent living facilities

Industry/Entity Type

Health Care

Contact Information for Business Card

Vellisant

Number of Pages Required

4 page

Font styles to use
Sans Serif

Colors

Designer to choose colors to be used in the design.

```html
<!DOCTYPE html>
<html lang="en">
<head>
<meta charset="utf-8">
<title>Vellisant – Quality health delivered at your door</title>
<link href="https://fonts.googleapis.com/css2?family=Arvo&family=Mulish:wght@400;600;700&display=swap" rel="stylesheet">
<style>
:root{
  --green-dark:#223203;
  --green-deep:#1b2902;
  --olive:#76902a;
  --orange:#f7a21b;
  --icon:#ef8d0c;
  --ink:#2a2a2a;
  --grey:#8a8a8a;
  --white:#ffffff;
}
*{box-sizing:border-box;margin:0;padding:0}
html,body{width:698px;height:1200px;overflow:hidden;background:var(--white)}
body{position:relative;font-family:"Mulish",sans-serif;color:var(--ink)}
.site-header{position:absolute;left:0;top:0;width:698px;height:66px;background:#fff;border-bottom:1px solid #e3e3e3}
.brand{position:absolute;left:45px;top:8px;width:80px;text-align:center}
.brand-dot{display:block;width:34px;height:34px;border-radius:50%;background:var(--olive);margin:0 auto 3px}
.brand-name{font-size:11px;font-weight:600;color:var(--green-dark);letter-spacing:.2px}
.call{position:absolute;left:363px;top:18px;display:flex;align-items:center;gap:6px}
.call-label{font-size:7.5px;font-weight:700;color:#333;letter-spacing:.3px}
.call-number{font-size:15px;font-weight:700;color:#222;line-height:1}
.divider{position:absolute;left:526px;top:20px;width:1px;height:26px;background:#ccc}
.social{position:absolute;left:542px;top:21px;display:flex;gap:4px}
.social span{width:24px;height:24px;border-radius:50%;border:1.5px solid #bbb}
.social span.on{background:var(--green-dark);border-color:var(--green-dark)}
.main-nav{position:absolute;left:45px;top:67px;height:30px;display:flex;align-items:center;font-size:8px;color:#333}
.nav-home{width:30px;height:30px;background:var(--orange);display:flex;align-items:center;justify-content:center;margin-right:8px}
.main-nav a{color:#333;text-decoration:none;margin-right:16px}
.hero{position:absolute;left:0;top:97px;width:698px;height:297px;background:linear-gradient(100deg,#ece8e2 0%,#e4ddd4 40%,#d7c9cc 60%,#eef0f2 80%,#cfd3da 100%)}
.hero-title{position:absolute;left:30px;top:103px;width:345px;height:90px;background:rgba(255,255,255,.72);padding:11px 0 0 16px;font-family:"Arvo",serif;font-size:23px;line-height:36px;color:#23320a}
.hero-rule{position:absolute;left:0;top:394px;width:698px;height:3px;background:var(--orange)}
.services{position:absolute;left:0;top:397px;width:698px;height:608px;background:var(--green-dark);color:#fff}
.services h2{position:absolute;top:27px;width:100%;text-align:center;font-weight:400;font-size:23px;letter-spacing:.5px}
.services p{position:absolute;left:70px;top:62px;width:558px;text-align:center;font-size:7.5px;line-height:14.5px}
.tile{position:absolute;width:145px;height:145px;background:#fff}
.tile-icon{position:absolute;left:48px;top:27px;width:50px;height:52px;border-radius:10px;background:var(--icon)}
.tile-label{position:absolute;left:0;bottom:0;width:145px;height:35px;background:var(--olive);display:flex;align-items:center;justify-content:center;text-align:center;font-size:11px;line-height:13px;padding:0 6px}
.tile.all{background:var(--olive);display:flex;align-items:center;justify-content:center;text-align:center;font-size:14px;line-height:18px}
.site-footer{position:absolute;left:0;top:1005px;width:698px;height:158px;background:var(--green-deep);color:#fff}
.col{position:absolute;top:26px}
.col h3{font-weight:400;font-size:12px;margin-bottom:12px;letter-spacing:.2px}
.contact-line{display:flex;gap:6px;font-size:8px;line-height:13px;margin-bottom:8px}
.news li{list-style:none;font-size:7.5px;margin-bottom:13.5px;padding-left:16px;position:relative}
.news li::before{content:"→";position:absolute;left:0;color:var(--olive)}
.quote{font-size:7.5px;line-height:14.5px;width:145px}
.quote-by{font-size:10px;margin-top:6px}
.foot-brand{position:absolute;left:536px;top:32px;width:88px;text-align:center}
.foot-brand .brand-dot{width:44px;height:44px;background:#7f8a70}
.foot-brand .brand-name{color:#fff;font-size:12px;font-weight:400}
.foot-social{position:absolute;left:526px;top:116px;display:flex;gap:3px}
.foot-social span{width:24px;height:24px;border-radius:50%}
.copyright{position:absolute;left:0;top:1163px;width:698px;height:37px;background:var(--orange);color:#fff;font-size:7.5px;display:flex;align-items:center;justify-content:center}
.copyright b{color:var(--green-dark);font-weight:600;margin:0 3px}
</style>
</head>
<body>
<header class="site-header">
  <div class="brand"><span class="brand-dot"></span><span class="brand-name">VELLISANT</span></div>
  <div class="call">
    <svg width="24" height="24" viewBox="0 0 24 24" fill="none" stroke="#222" stroke-width="1.4"><path d="M5 3l3 0 2 5-2 1.5a11 11 0 0 0 6 6L15.5 13l5 2v3a2 2 0 0 1-2 2A16 16 0 0 1 3 5a2 2 0 0 1 2-2z"/><path d="M14 3a7 7 0 0 1 7 7M14 6.5a3.5 3.5 0 0 1 3.5 3.5"/></svg>
    <div><div class="call-label">CALL US NOW ON :</div><div class="call-number">(555) 018-2046</div></div>
  </div>
  <div class="divider"></div>
  <div class="social"><span class="on"></span><span></span><span></span><span></span></div>
</header>
<nav class="main-nav">
  <span class="nav-home"><svg width="14" height="12" viewBox="0 0 14 12"><path d="M7 0l7 6h-2v6H9V8H5v4H2V6H0z" fill="#223203"/></svg></span>
  <a>Assisted Living</a><a>Skilled Nursing</a><a>Independent Living</a><a>Home &amp; Community Based Living</a><a>Respite Care</a><a>Rehabilitation</a><a>Kelora Learning</a>
</nav>
<section class="hero" role="img" aria-label="Photo of a smiling nurse caring for a seated older woman">
  <h1 class="hero-title" style="font-weight:400">Motivating Independent<br>Living &amp; Community Living</h1>
</section>
<div class="hero-rule"></div>
<section class="services">
  <h2>STAY HOME</h2>
  <p>Vellisant offers home and Community Based Services for adults who wish to continue to live independently in the comfort of their communities. We provide on site services and deliver high quality healthcare at your door. Our experienced physicians coordinate care with our certified nurse practitioners and provide chronic care management, physical therapy, rehabilitation and medications management.</p>
  <div class="tile" style="left:46px;top:125px"><div class="tile-icon" role="img" aria-label="Medical bag icon"></div><div class="tile-label">Comprehensive primary Care Services</div></div>
  <div class="tile" style="left:199px;top:125px"><div class="tile-icon" role="img" aria-label="Specialist with plus sign icon"></div><div class="tile-label">Coordination of Specialty Care</div></div>
  <div class="tile" style="left:353px;top:125px"><div class="tile-icon" role="img" aria-label="Patient on bed icon"></div><div class="tile-label">Chronic<br>Disease Management</div></div>
  <div class="tile" style="left:507px;top:125px"><div class="tile-icon" role="img" aria-label="Caregiver pushing wheelchair icon"></div><div class="tile-label">Transitional Care</div></div>
  <div class="tile" style="left:46px;top:278px"><div class="tile-icon" role="img" aria-label="Nurse icon"></div><div class="tile-label">Skilled Nursing</div></div>
  <div class="tile" style="left:199px;top:278px"><div class="tile-icon" role="img" aria-label="Older couple icon"></div><div class="tile-label">Social Services Assessment</div></div>
  <div class="tile" style="left:353px;top:278px"><div class="tile-icon" role="img" aria-label="House with caring hands icon"></div><div class="tile-label">Home Health Assistance</div></div>
  <div class="tile" style="left:507px;top:278px"><div class="tile-icon" role="img" aria-label="Therapist treating patient icon"></div><div class="tile-label">Physical Therapy</div></div>
  <div class="tile" style="left:46px;top:432px"><div class="tile-icon" role="img" aria-label="Head with brain icon"></div><div class="tile-label">Mental Health</div></div>
  <div class="tile" style="left:199px;top:432px"><div class="tile-icon" role="img" aria-label="Dental chair icon"></div><div class="tile-label">Dental Health</div></div>
  <div class="tile" style="left:353px;top:432px"><div class="tile-icon" role="img" aria-label="Van icon" style="left:30px;width:86px;height:44px;top:32px"></div><div class="tile-label">Transportation</div></div>
  <div class="tile all" style="left:507px;top:432px">VIEW ALL<br>SERVICES</div>
</section>
<footer class="site-footer">
  <div class="col" style="left:47px">
    <h3>CONTACT US</h3>
    <div class="contact-line"><svg width="9" height="12" viewBox="0 0 9 12"><path d="M4.5 0A4.5 4.5 0 0 0 0 4.5C0 8 4.5 12 4.5 12S9 8 9 4.5A4.5 4.5 0 0 0 4.5 0zm0 6.3a1.8 1.8 0 1 1 0-3.6 1.8 1.8 0 0 1 0 3.6z" fill="#fff"/></svg><div><span style="font-size:9.5px">VELLISANT</span><br>123 Building name, Street Name,<br>City, Country - Zipcode</div></div>
    <div class="contact-line" style="font-weight:700;font-size:9px"><svg width="10" height="10" viewBox="0 0 24 24"><path d="M5 2h4l2 5-2.5 1.5a11 11 0 0 0 7 7L17 13l5 2v4a2 2 0 0 1-2 2A18 18 0 0 1 3 4a2 2 0 0 1 2-2z" fill="#fff"/></svg>555-018-2046</div>
    <div class="contact-line"><svg width="10" height="9" viewBox="0 0 10 8" fill="none" stroke="#fff"><rect x=".5" y=".5" width="9" height="7"/><path d="M.5.5L5 4.5 9.5.5"/></svg>info@vellisant.com</div>
  </div>
  <div class="col" style="left:201px">
    <h3>LATEST NEWS</h3>
    <ul class="news"><li>Lorem ipsum is simply dummy</li><li>Lorem ipsum is simply dummy</li><li>Lorem ipsum is simply dummy</li><li>Lorem ipsum is simply dummy</li></ul>
  </div>
  <div class="col" style="left:355px">
    <h3>TESTIMONIALS</h3>
    <div class="quote">"Lorem Ipsum is simply dummy text of the printing and typesetting industry. Lorem Ipsum has been the industry's standard."</div>
    <div class="quote-by">- Marta Ilves.</div>
  </div>
  <div class="foot-brand"><span class="brand-dot"></span><span class="brand-name">VELLISANT</span></div>
  <div class="foot-social"><span style="background:#3b5998"></span><span style="background:#1da1f2"></span><span style="background:#dd4b39"></span><span style="background:#0e76a8"></span></div>
</footer>
<div class="copyright">© <b>VELLISANT</b> - 2017. All Rights Reserved.</div>
</body>
</html>
```